UL Aesthetic improvement on full website

brightneighbourhq.com
We need someone to improve the current website brightneighbourhq.com
Some designed to fail to follow isntruction and deliver. please find attached summary latest design requirement, please follow and read each of the requirements carefully and submit max two versions only. The winner would have to deliver within 5 days

Sample reference : velmorq.com/html/brightneighbour/#
(previous winner cant deliver)
*All of our wording and graphic content are updated, designer wouldn't involve in recreating any content.
Designer may use template or own material. delivery in html and implement on our WordPress server

please submit about us the project submission.
upon the winning, you have to maintain sub content / pages and submit the full site with your improved version of full websites including inner pages

Low design quality

Target Market(s)

general audience

Industry/Entity Type

social service

Number of Pages Required

5+ page

Requirements
Must have
• feeling and look similar to pobrix dot com
Nice to have
• extend the same style to other pages

```html
<!DOCTYPE html>
<html lang="en">
<head>
<meta charset="utf-8">
<title>Bright Neighbour — New Way of Giving</title>
<link href="https://fonts.googleapis.com/css2?family=Montserrat:wght@500;600;700&family=Roboto:wght@400;500;700&display=swap" rel="stylesheet">
<style>
:root{
  --coral:#f26d6d;
  --coral-soft:#f47d7d;
  --ink:#151515;
  --body:#555;
  --grey-bg:#f7f7f7;
  --pink-bg:#fff3f4;
  --pink-hero:#ffd3d6;
  --footer-bg:#fde3e3;
  --white:#fff;
}
*{box-sizing:border-box;margin:0;padding:0}
html,body{width:1200px;height:2874px;overflow:hidden}
body{position:relative;background:var(--white);font-family:'Roboto',sans-serif;color:var(--body)}
.abs{position:absolute}
.heading{font-family:'Montserrat',sans-serif;font-weight:700}
.section-title{font-family:'Montserrat',sans-serif;font-weight:700;color:var(--coral);font-size:33px;letter-spacing:.3px}
.btn-outline{position:absolute;border:2.5px solid var(--coral);border-radius:26px;display:flex;align-items:center;justify-content:center;font-family:'Roboto',sans-serif;font-weight:700;font-size:15.5px;color:var(--ink);background:var(--white)}
.brand-name{position:absolute;display:flex;align-items:center;gap:9px;font-family:'Montserrat',sans-serif;font-weight:700;font-size:18px;color:var(--coral);white-space:nowrap}
.brand-name i{display:block;width:16px;height:16px;border-radius:50%;background:var(--coral)}

/* hero */
.hero{position:absolute;left:0;top:0;width:1200px;height:619px;background:var(--grey-bg);overflow:hidden}
.hero-circle{position:absolute;left:580px;top:-89px;width:624px;height:624px;border-radius:50%;background:var(--pink-hero)}
.nav{position:absolute;top:31px;font-family:'Roboto',sans-serif;font-weight:500;font-size:16px;color:var(--ink);letter-spacing:.3px}
.nav span{position:absolute;white-space:nowrap}
.login{position:absolute;left:950px;top:17px;width:138px;height:48px;border-radius:24px;background:var(--coral);color:var(--white);font-weight:700;font-size:16px;display:flex;align-items:center;justify-content:center;gap:10px}
.hero-kicker{left:111px;top:246px;font-family:'Montserrat',sans-serif;font-weight:600;font-size:20px;color:var(--coral-soft)}
.hero-title{left:110px;top:277px;font-size:38px;color:var(--ink);letter-spacing:.5px}
.phones{position:absolute;left:619px;top:106px}

/* intro */
.media{position:absolute;border-radius:12px}
.intro-text{left:665px;top:820px;width:424px;font-size:15.5px;line-height:25px;text-align:justify}

/* values */
.values{position:absolute;left:0;top:1169px;width:1200px;height:468px;background:var(--pink-bg)}
.card{position:absolute;top:136px;width:315px;height:268px;background:var(--white);border-radius:8px;box-shadow:0 2px 10px rgba(0,0,0,.05);text-align:center}
.card .icon{width:87px;height:87px;border-radius:50%;margin:20px auto 0;display:flex;align-items:center;justify-content:center}
.card h3{font-family:'Roboto',sans-serif;font-weight:700;font-size:20px;color:var(--ink);margin-top:19px;letter-spacing:.2px}
.card p{font-size:15px;line-height:23px;margin:14px 16px 0}

/* story */
.story-text{left:111px;top:1830px;width:425px;font-size:15.5px;line-height:24px;text-align:justify}

/* partners */
.partners{position:absolute;left:0;top:2189px;width:1200px;height:299px;background:var(--grey-bg)}
.partner{position:absolute;top:146px;width:183px;height:87px;background:var(--white);border-radius:6px;box-shadow:0 2px 8px rgba(0,0,0,.05);display:flex;align-items:center;justify-content:center;gap:8px;font-family:'Roboto',sans-serif;font-weight:700;font-size:17px;color:#3d3d3d}
.partner i{display:block;width:14px;height:14px;border-radius:50%;background:var(--coral)}

/* footer */
.footer{position:absolute;left:0;top:2488px;width:1200px;height:386px;background:var(--footer-bg)}
.social{position:absolute;top:51px;width:38px;height:38px;border-radius:50%;background:var(--white);box-shadow:0 1px 4px rgba(0,0,0,.06)}
.social::after{content:"";position:absolute;left:13px;top:13px;width:12px;height:12px;border-radius:50%;border:1.6px solid var(--coral)}
.foot-head{position:absolute;top:126px;font-family:'Roboto',sans-serif;font-weight:700;font-size:19px;color:var(--ink)}
.foot-links{position:absolute;top:173px;list-style:none;font-size:15.5px;line-height:25px;color:#555}
.field{position:absolute;top:176px;width:206px;height:49px;border-radius:25px;background:var(--white);font-size:15.5px;color:#555;display:flex;align-items:center;padding-left:17px;font-weight:500}
.subscribe{position:absolute;left:664px;top:238px;width:424px;height:48px;border-radius:24px;background:var(--coral);color:var(--white);font-weight:700;font-size:16px;display:flex;align-items:center;justify-content:center;letter-spacing:.3px}
.divider{position:absolute;left:111px;top:323px;width:977px;height:1px;background:#f2c9c9}
.copyright{position:absolute;left:0;width:1200px;top:341px;text-align:center;font-size:14px;color:#555}
</style>
</head>
<body>

<header class="hero">
  <div class="hero-circle"></div>
  <div class="brand-name" style="left:111px;top:29px"><i></i>Bright Neighbour</div>
  <nav class="nav">
    <span style="left:362px">HOME</span>
    <span style="left:441px">BOUT US</span>
    <span style="left:542px">OUR STORY</span>
    <span style="left:664px">SOCIAL IMPACT</span>
    <span style="left:819px">JOIN US&nbsp;&nbsp;
      <svg width="12" height="8" viewBox="0 0 12 8"><path d="M2 2l4 4 4-4" fill="none" stroke="#151515" stroke-width="1.6"/></svg></span>
  </nav>
  <div class="login">
    <svg width="18" height="18" viewBox="0 0 18 18"><circle cx="9" cy="9" r="7.5" fill="none" stroke="#fff" stroke-width="1.6"/><circle cx="9" cy="7.5" r="2.6" fill="none" stroke="#fff" stroke-width="1.4"/><path d="M4.5 14c1.5-2.5 7.5-2.5 9 0" fill="none" stroke="#fff" stroke-width="1.4"/></svg>
    LOGIN
  </div>
  <div class="abs hero-kicker">NEW WAY OF GIVING</div>
  <h1 class="abs heading hero-title">SOCIAL INCLUSION</h1>
  <div class="btn-outline" style="left:111px;top:350px;width:168px;height:48px">PAY-IT-FORWARD</div>

  <svg class="phones" width="463" height="446" viewBox="0 0 463 446" role="img" aria-label="Three phones showing the app's merchant, order and home screens">
    <defs>
      <linearGradient id="scr" x1="0" y1="0" x2="0" y2="1"><stop offset="0" stop-color="#fbd6d8"/><stop offset=".3" stop-color="#ffffff"/><stop offset="1" stop-color="#f7f1ee"/></linearGradient>
      <linearGradient id="scrM" x1="0" y1="0" x2="0" y2="1"><stop offset="0" stop-color="#fde9b0"/><stop offset=".25" stop-color="#fff"/><stop offset="1" stop-color="#f6efe7"/></linearGradient>
    </defs>
    <rect x="0" y="58" width="192" height="390" rx="26" fill="#2a2a2a"/>
    <rect x="8" y="66" width="176" height="374" rx="20" fill="url(#scr)"/>
    <rect x="268" y="58" width="195" height="390" rx="26" fill="#2a2a2a"/>
    <rect x="276" y="66" width="179" height="374" rx="20" fill="url(#scr)"/>
    <rect x="128" y="0" width="192" height="390" rx="26" fill="#1f1f1f"/>
    <rect x="136" y="8" width="176" height="374" rx="20" fill="url(#scrM)"/>
    <rect x="190" y="8" width="68" height="14" rx="7" fill="#1f1f1f"/>
  </svg>
</header>

<section>
  <div class="media" style="left:110px;top:716px;width:489px;height:360px;background:linear-gradient(180deg,#a9cdd3 0%,#c7d3d6 40%,#ebb7b6 70%,#e39c9f 100%)" role="img" aria-label="Video: illustrated city skyline with a path of children bridging the gap for those who fall between the cracks"></div>
  <svg class="abs" style="left:317px;top:858px" width="76" height="76" viewBox="0 0 76 76"><circle cx="38" cy="38" r="36" fill="#fff" fill-opacity=".9" stroke="#fff" stroke-width="2"/><path d="M32 28l14 10-14 10z" fill="#f26d6d"/></svg>
  <h2 class="abs section-title" style="left:664px;top:760px;font-size:26px">HELLO, BRIGHT NEIGHBOURS!</h2>
  <p class="abs intro-text">Just like you, we resonate with a variety of social causes. At the core of everything, we believe that many societal challenges could be minimized merely by being more kind to one another and showing more trust in each other, especially during these difficult times.</p>
  <div class="btn-outline" style="left:665px;top:977px;width:136px;height:48px">READ MORE</div>
</section>

<section class="values">
  <h2 class="abs section-title" style="left:0;width:1200px;text-align:center;top:57px">SOCIAL INCLUSION</h2>
  <div class="card" style="left:111px">
    <div class="icon" style="background:#fde6e6">
      <svg width="48" height="48" viewBox="0 0 48 48" fill="none" stroke="#f26d6d" stroke-width="1.6"><path d="M24 34c-8-6-12-10-12-15a6 6 0 0112-2 6 6 0 0112 2c0 5-4 9-12 15z"/><path d="M6 26l6 12h6M42 26l-6 12h-6"/></svg>
    </div>
    <h3>OUR PHILOSOPHY</h3>
    <p>We believe in authentic social responsibility is driven from individuals and businesses.</p>
  </div>
  <div class="card" style="left:443px">
    <div class="icon" style="background:#fdf5dc">
      <svg width="48" height="48" viewBox="0 0 48 48" fill="none" stroke="#e8c43c" stroke-width="1.6"><circle cx="24" cy="24" r="16"/><circle cx="24" cy="24" r="10"/><circle cx="24" cy="24" r="4"/><path d="M24 24l14-14M34 10h4v4"/></svg>
    </div>
    <h3>OUR MISSION</h3>
    <p>We connect individuals and businesses to support where it needs most in an easy, transparent, and holistic way through our platform.</p>
  </div>
  <div class="card" style="left:773px">
    <div class="icon" style="background:#efe9fb">
      <svg width="48" height="48" viewBox="0 0 48 48" fill="none" stroke="#9b82d8" stroke-width="1.6"><circle cx="24" cy="24" r="14"/><path d="M10 24h28M24 10c-5 5-5 23 0 28M24 10c5 5 5 23 0 28"/></svg>
    </div>
    <h3>OUR FUTURE</h3>
    <p>Together, social impact as part of DNA at the heart of every consumption and business.</p>
  </div>
</section>

<section>
  <h2 class="abs section-title" style="left:111px;top:1766px;font-size:30px">OUR STORY</h2>
  <p class="abs story-text">Back in the 1980s, my family received generous donations and small handwritten notes containing good wishes through a newspaper fund raising for my mum's medical expenses. I vividly remember some old and tattered notes from strangers. We ended up with double the amount that was needed, and my parents used the remaining sum to support other patients.</p>
  <div class="btn-outline" style="left:111px;top:2002px;width:136px;height:48px">READ MORE</div>
  <div class="media" style="left:600px;top:1732px;width:489px;height:360px;background:linear-gradient(180deg,#e1f1f9 0%,#e6eef2 50%,#f3c4c6 80%,#e8a7ae 100%)" role="img" aria-label="Illustration of cheerful neighbours among flowers in front of the city skyline"></div>
</section>

<section class="partners">
  <h2 class="abs section-title" style="left:0;width:1200px;text-align:center;top:60px">OUR PARTNERS</h2>
  <svg class="abs" style="left:48px;top:175px" width="20" height="30" viewBox="0 0 20 30"><path d="M15 3L4 15l11 12" fill="none" stroke="#aaa" stroke-width="2.4"/></svg>
  <div class="partner" style="left:111px"><i></i>Arkwell</div>
  <div class="partner" style="left:310px">Ridepath</div>
  <div class="partner" style="left:508px"><i style="border-radius:2px"></i>Harbrix Bank</div>
  <div class="partner" style="left:707px">Solent Institute</div>
  <div class="partner" style="left:904px">Meridane Ventures</div>
  <svg class="abs" style="left:1132px;top:175px" width="20" height="30" viewBox="0 0 20 30"><path d="M5 3l11 12L5 27" fill="none" stroke="#f26d6d" stroke-width="2.4"/></svg>
</section>

<footer class="footer">
  <div class="brand-name" style="left:111px;top:60px"><i></i>Bright Neighbour</div>
  <span class="social" style="left:920px"></span>
  <span class="social" style="left:963px"></span>
  <span class="social" style="left:1006px"></span>
  <span class="social" style="left:1049px"></span>

  <div class="foot-head" style="left:111px">Get To Know Us</div>
  <ul class="foot-links" style="left:111px">
    <li>Home</li><li>About Us</li><li>Our Story</li><li>Social Impact</li><li>Bright Neighbour</li>
  </ul>
  <div class="foot-head" style="left:361px">Quick Links</div>
  <ul class="foot-links" style="left:361px">
    <li>Bright Business</li><li>Merchant</li><li>The Bright Gift</li><li>FAQs</li><li>Contact Us</li>
  </ul>
  <div class="foot-head" style="left:664px">Subscribe Our Newsletter</div>
  <div class="field" style="left:664px">Name</div>
  <div class="field" style="left:880px;width:208px">Email Address</div>
  <div class="subscribe">SUBSCRIBE</div>
  <div class="divider"></div>
  <div class="copyright">© 2021 Company Name. All Rights Reserved</div>
</footer>

</body>
</html>
```